Vorlanta PowerPoint Template

I have a company called Vorlanta, LLC and my company logo is already designed. I need a PowerPoint template that I will be using to pitch potential investors and business partners. This should be a very professional-looking template that leverages the company logo colors and really pops. The company is an AI product research and development company.

```html
<!DOCTYPE html>
<html lang="en">
<head>
<meta charset="UTF-8">
<title>Vorlanta – Presentation Template</title>
<link rel="stylesheet" href="https://fonts.googleapis.com/css2?family=Archivo+Black&family=Poppins:wght@300;400;500;600&family=Allura&display=swap">
<style>
  :root{
    --page:#e3e3e3;
    --ink:#ffffff;
    --dark:#120204;
    --deep:#1d0407;
    --red:#e8121c;
    --red-soft:#ff2a3a;
    --muted:rgba(255,255,255,.9);
    --blob-a:#ff8f4a;
    --blob-b:#ff3a5a;
    --blob-c:#d81f7e;
  }
  *{box-sizing:border-box;margin:0;padding:0}
  html,body{width:1200px;height:1064px;overflow:hidden;background:var(--page)}
  body{position:relative;font-family:"Poppins",sans-serif;color:var(--ink)}

  .slide{position:absolute;width:534px;height:300px;overflow:hidden;
    background:linear-gradient(135deg,var(--dark) 0%,var(--deep) 55%,#3a0509 100%);
    box-shadow:0 10px 28px rgba(0,0,0,.28)}
  .slide--title{left:333px;top:63px;height:301px;
    background:radial-gradient(ellipse at 80% 90%,#6a0a0e 0%,transparent 55%),linear-gradient(135deg,#0d0103 0%,#1f0307 60%,#3a0509 100%)}
  .slide--about{left:57px;top:382px}
  .slide--services{left:609px;top:382px}
  .slide--team{left:57px;top:700px;
    background:radial-gradient(ellipse at 55% 0%,#7a0a0f 0%,transparent 60%),linear-gradient(135deg,#1a0205 0%,#2b0408 60%,#120104 100%)}
  .slide--clients{left:609px;top:700px;
    background:radial-gradient(ellipse at 100% 0%,#8a0b10 0%,transparent 55%),linear-gradient(135deg,#0f0103 0%,#250408 60%,#3a0509 100%)}

  .heading{position:absolute;font-family:"Archivo Black",sans-serif;font-size:28px;line-height:1;letter-spacing:-.6px;text-transform:uppercase}
  .body-copy{position:absolute;font-weight:300;font-size:8px;line-height:10.7px;letter-spacing:-.15px;white-space:nowrap;color:var(--muted)}

  .blob{position:absolute;border-radius:58% 42% 52% 48% / 50% 55% 45% 50%;
    background:linear-gradient(150deg,var(--blob-a) 0%,var(--blob-b) 50%,var(--blob-c) 100%);opacity:.92}
  .photo{position:absolute}

  /* title slide */
  .brand{position:absolute;left:31px;top:36px;display:flex;align-items:center;gap:8px}
  .brand__mark{width:28px;height:28px;border-radius:50%;background:var(--red)}
  .brand__name{font-weight:600;font-size:23px;letter-spacing:-.4px;color:var(--ink)}
  .hero-title{position:absolute;left:30px;top:98px;font-family:"Archivo Black",sans-serif;font-size:26px;line-height:26px;letter-spacing:-.3px}
  .hero-title--ghost{left:18px;top:104px;color:transparent;-webkit-text-stroke:.7px rgba(255,255,255,.35)}
  .tagline{position:absolute;left:30px;top:184px;font-size:15.5px;line-height:19px;font-weight:500}
  .tagline em{font-style:normal;color:var(--red-soft)}
  .tagline .script{font-family:"Allura",cursive;font-size:32px;font-weight:400;position:relative;top:8px;margin-left:2px}

  /* about */
  .mission-title{position:absolute;left:47px;top:196px;font-family:"Archivo Black",sans-serif;font-size:27px;line-height:30px;color:var(--red)}
  .mission-icon{position:absolute;left:122px;top:179px}
  .panel{position:absolute;background:rgba(255,255,255,.09);border-radius:4px}

  /* services */
  .service{position:absolute;width:77px;height:60px;background:rgba(255,255,255,.12);border-radius:4px;
    display:flex;flex-direction:column;align-items:center;justify-content:center;gap:3px;text-align:center;font-weight:500;font-size:9.4px;line-height:11px}

  /* team */
  .role-line{position:absolute;left:43px;top:76px;font-weight:600;font-size:9.5px}
  .member{position:absolute;top:149px;width:83px;height:129px}
  .member__card{position:absolute;left:0;top:30px;width:83px;height:99px;background:rgba(255,255,255,.10);border-radius:6px}
  .member__photo{position:absolute;left:6px;top:0;width:70px;height:70px;border-radius:50%;border:1.5px solid var(--red);
    background:linear-gradient(180deg,#f1f1f1 0%,#d8d2cf 100%)}
  .member__name{position:absolute;left:0;top:86px;width:100%;text-align:center;font-weight:600;font-size:8.6px}
  .member__role{position:absolute;left:0;top:99px;width:100%;text-align:center;font-size:8.4px;line-height:10px;color:var(--muted)}

  /* clients */
  .quote{position:absolute;font-weight:300;font-size:8px;line-height:10.7px;letter-spacing:-.1px;white-space:nowrap;color:var(--muted)}
  .quote-mark{position:absolute;font-family:"Archivo Black",sans-serif;color:var(--ink);line-height:1}
  .quote-mark--inline{position:relative;top:4px;margin-left:10px;font-size:14px}
</style>
</head>
<body>

<!-- Title slide -->
<section class="slide slide--title">
  <div class="photo" role="img" aria-label="Glowing red AI processor chip with particles" style="left:230px;top:20px;width:304px;height:281px;background:radial-gradient(ellipse at 55% 45%,rgba(255,60,50,.85) 0%,rgba(190,20,25,.55) 22%,rgba(90,8,12,.3) 48%,transparent 70%)"></div>
  <div class="brand"><span class="brand__mark"></span><span class="brand__name">Vorlanta</span></div>
  <h1 class="hero-title hero-title--ghost" aria-hidden="true">AI<br>DEVELOPMENT<br>COMPANY</h1>
  <h1 class="hero-title">AI<br>DEVELOPMENT<br>COMPANY</h1>
  <p class="tagline">Crafting <em>Intelligence</em>,<br>Crafting the <span class="script">Future</span></p>
</section>

<!-- About slide -->
<section class="slide slide--about">
  <div class="photo" role="img" aria-label="Humanoid robot in helmet, side profile" style="left:348px;top:0;width:186px;height:300px;background:radial-gradient(ellipse at 45% 40%,#6f9c98 0%,#2e4a49 35%,#120406 75%)"></div>
  <div class="blob" role="img" aria-label="Decorative gradient shape" style="left:-18px;top:252px;width:70px;height:60px"></div>
  <div class="blob" role="img" aria-label="Decorative gradient shape" style="left:300px;top:136px;width:44px;height:36px;opacity:.35;filter:blur(6px)"></div>
  <h2 class="heading" style="left:41px;top:40px">About Us</h2>
  <p class="body-copy" style="left:41px;top:79px">Lorem Ipsum is simply dummy text of the<br>printing and typesetting industry. Lorem<br>Ipsum has been the industry's standard<br>dummy text ever since the 1500s, when an<br>unknown printer took a galley of type and<br>scrambled it to make a type specimen.</p>
  <h3 class="mission-title">OUR<br>MISSION</h3>
  <svg class="mission-icon" width="34" height="34" viewBox="0 0 34 34" fill="none" stroke="#fff" stroke-width="2">
    <circle cx="15" cy="15" r="12"/><circle cx="15" cy="15" r="7.5"/><circle cx="15" cy="15" r="3"/>
    <path d="M15 15 L30 30 M24 30 h6 v-6"/>
  </svg>
  <div class="panel" style="left:165px;top:174px;width:199px;height:96px"></div>
  <p class="body-copy" style="left:182px;top:192px">Lorem Ipsum is simply dummy text of the<br>printing and typesetting industry. Lorem<br>Ipsum has been the industry's standard<br>dummy text ever since the 1500s, when an<br>unknown printer took a galley of type and<br>scrambled it to make a type specimen.</p>
</section>

<!-- Services slide -->
<section class="slide slide--services">
  <div class="photo" role="img" aria-label="Man wearing VR headset touching holographic interface" style="left:265px;top:23px;width:300px;height:300px;border-radius:50%;background:radial-gradient(circle at 55% 45%,#6a3c7a 0%,#3a2150 40%,#1b0a20 80%)"></div>
  <div class="blob" role="img" aria-label="Decorative gradient shape" style="left:-22px;top:-18px;width:60px;height:62px"></div>
  <div class="blob" role="img" aria-label="Decorative gradient shape" style="left:350px;top:10px;width:60px;height:52px"></div>
  <div class="blob" role="img" aria-label="Decorative gradient shape" style="left:253px;top:250px;width:100px;height:70px"></div>
  <div class="blob" role="img" aria-label="Decorative gradient shape" style="left:110px;top:292px;width:70px;height:30px;opacity:.8"></div>
  <h2 class="heading" style="left:41px;top:40px">Our Services</h2>
  <p class="body-copy" style="left:42px;top:72px">Lorem Ipsum is simply dummy text of the printing and<br>typesetting industry. Lorem Ipsum has been the industry's<br>standard dummy text ever since the 1500s.</p>
  <div class="service" style="left:42px;top:126px">
    <svg width="18" height="18" viewBox="0 0 18 18" fill="none" stroke="#fff" stroke-width="1.2"><rect x="3" y="5" width="12" height="9" rx="2"/><circle cx="7" cy="9" r="1"/><circle cx="11" cy="9" r="1"/><path d="M9 5V2M1 9h2M15 9h2M7 12h4"/></svg>
    <span>Generate<br>AI</span></div>
  <div class="service" style="left:143px;top:126px">
    <svg width="18" height="18" viewBox="0 0 18 18" fill="none" stroke="#fff" stroke-width="1.2"><circle cx="9" cy="9" r="3"/><circle cx="9" cy="9" r="6"/><path d="M9 1v2M9 15v2M1 9h2M15 9h2M3.3 3.3l1.4 1.4M13.3 13.3l1.4 1.4M3.3 14.7l1.4-1.4M13.3 4.7l1.4-1.4"/></svg>
    <span>Automated<br>Optimization</span></div>
  <div class="service" style="left:42px;top:211px">
    <svg width="18" height="18" viewBox="0 0 18 18" fill="none" stroke="#fff" stroke-width="1.2"><path d="M8 2.5a3 3 0 0 0-5 2 3 3 0 0 0-1 5 3 3 0 0 0 3 4.5h3zM10 2.5a3 3 0 0 1 5 2 3 3 0 0 1 1 5 3 3 0 0 1-3 4.5h-3z"/><path d="M11 7h3M11 10h2M4 7h3"/></svg>
    <span>Deep<br>Learning</span></div>
  <div class="service" style="left:143px;top:211px">
    <svg width="18" height="18" viewBox="0 0 18 18" fill="none" stroke="#fff" stroke-width="1.2"><circle cx="9" cy="9" r="7"/><rect x="5.5" y="5.5" width="7" height="7" rx="1"/><path d="M9 2v3.5M9 12.5V16M2 9h3.5M12.5 9H16"/></svg>
    <span>Machine<br>Learning</span></div>
</section>

<!-- Team slide -->
<section class="slide slide--team">
  <div class="photo" role="img" aria-label="Portrait of the CEO in a dark suit, arms crossed" style="left:375px;top:47px;width:141px;height:253px;border-radius:60px 60px 0 0;background:linear-gradient(180deg,#5a3a2e 0%,#2a1c1a 30%,#111 60%,#0a0a0a 100%)"></div>
  <div class="blob" role="img" aria-label="Decorative gradient shape" style="left:488px;top:-8px;width:62px;height:44px"></div>
  <div class="blob" role="img" aria-label="Decorative gradient shape" style="left:-24px;top:262px;width:70px;height:56px"></div>
  <div class="blob" role="img" aria-label="Decorative gradient shape" style="left:348px;top:222px;width:40px;height:34px;opacity:.35;filter:blur(6px)"></div>
  <h2 class="heading" style="left:42px;top:40px">Our Team</h2>
  <p class="role-line">CEO [ NAME ]</p>
  <p class="body-copy" style="left:43px;top:93px">Lorem Ipsum is simply dummy text of the printing and<br>typesetting industry. Lorem Ipsum has been the industry's<br>standard dummy text ever since the 1500s.</p>
  <div class="member" style="left:43px"><div class="member__card"></div><div class="member__photo" role="img" aria-label="Team member portrait"></div><p class="member__name">Lorem Ipsum</p><p class="member__role">Manager</p></div>
  <div class="member" style="left:152px"><div class="member__card"></div><div class="member__photo" role="img" aria-label="Team member portrait"></div><p class="member__name">Lorem Ipsum</p><p class="member__role">Director of<br>Projects</p></div>
  <div class="member" style="left:260px"><div class="member__card"></div><div class="member__photo" role="img" aria-label="Team member portrait"></div><p class="member__name">Lorem Ipsum</p><p class="member__role">Director of<br>Accounts</p></div>
</section>

<!-- Clients slide -->
<section class="slide slide--clients">
  <div class="blob" role="img" aria-label="Decorative gradient shape" style="left:-30px;top:236px;width:72px;height:80px"></div>
  <div class="blob" role="img" aria-label="Decorative gradient shape" style="left:466px;top:244px;width:90px;height:72px"></div>
  <h2 class="heading" style="left:43px;top:40px;line-height:31px">Our Happy<br>Clients</h2>
  <div class="photo" role="img" aria-label="Robotic hand shaking a human hand over red network lines" style="left:268px;top:62px;width:227px;height:148px;border:1px solid rgba(255,255,255,.6);border-radius:5px;background:radial-gradient(ellipse at 45% 55%,#c8b8e8 0%,#8a3040 30%,#4a0509 70%)"></div>
  <span class="quote-mark" style="left:44px;top:120px;font-size:14px">&ldquo;</span>
  <p class="quote" style="left:55px;top:134px">Lorem Ipsum is simply dummy text of<br>the printing and typesetting industry.<br>Lorem Ipsum has been the industry's<br>standard dummy text.<span class="quote-mark quote-mark--inline">&rdquo;</span></p>
  <span class="quote-mark" style="left:154px;top:197px;font-size:22px">&ldquo;</span>
  <div class="panel" style="left:161px;top:204px;width:196px;height:66px"></div>
  <p class="quote" style="left:161px;top:216px;width:196px;text-align:center">Lorem Ipsum is simply dummy text of<br>the printing and typesetting industry.<br>Lorem Ipsum has been the industry's<br>standard dummy text.</p>
  <span class="quote-mark" style="left:332px;top:266px;font-size:22px">&rdquo;</span>
</section>

</body>
</html>
```